New Business Card for Web Design/Internet Marketing Company

Looking for a great looking new business card. We are a 10 year old web design, internet marketing and website management company that works mostly with small businesses.

Our new card needs to better match the colors and style of our website, be bold, extremely usable and slightly edgy.

Target Market(s)

Small/Medium businesses that have websites

Industry/Entity Type

Internet

Requirements
Must have
• Front and back design, full color, rounded corners please

Must use the colors/style of our website (JPG provided)

INFO FOR CARDS (as readable as possible please)
Mark Lenner
President/CEO
mark@trelvanmedia.example
Phone: 520-381-7459
Toll Free: 866-381-7459
Address: 4315 W. Calloway Ave. Ste. 140, Tucson, AZ 85792

THINGS I WANT TO PROMOTE (if there is room):
1. Our Website - www.trelvanmedia.example

2. Social Media
Twitter: @trelvanmedia
Facebook: www.facebook.com/trelvanmedia

3. Our Services
Web Design
Internet Marketing
Website Management

```html
<!DOCTYPE html>
<html lang="en">
<head>
<meta charset="utf-8">
<title>Trelvan Media – Business Card</title>
<link rel="stylesheet" href="https://fonts.googleapis.com/css2?family=Open+Sans:ital,wght@0,400;0,600;0,700;1,400&display=swap">
<style>
  :root {
    --navy-deep: #13256a;
    --navy: #1d3f93;
    --navy-light: #2a58b8;
    --orange: #f28a1e;
    --sky: #2f9fd9;
    --white: #ffffff;
    --page: #e9ebef;
    --ink-soft: #dfe6f5;
  }
  * { box-sizing: border-box; margin: 0; padding: 0; }
  html, body {
    width: 1200px; height: 944px; overflow: hidden;
    background: var(--page);
    font-family: "Open Sans", Arial, sans-serif;
  }
  .canvas { position: relative; width: 1200px; height: 944px; }

  .card {
    position: absolute;
    width: 620px; height: 354px;
    border-radius: 26px;
    overflow: hidden;
    box-shadow: 0 10px 28px rgba(10, 20, 50, 0.25);
  }

  /* Front */
  .card-front {
    left: 70px; top: 60px;
    background: radial-gradient(ellipse at 45% 40%, var(--navy-light) 0%, var(--navy) 45%, var(--navy-deep) 100%);
  }
  .brand {
    display: flex; align-items: center; gap: 16px;
  }
  .brand-dot {
    width: 46px; height: 46px; border-radius: 50%;
    background: var(--sky);
    flex: none;
  }
  .brand-name {
    font-weight: 700; font-size: 54px; letter-spacing: -1px;
    color: var(--orange); line-height: 1;
  }
  .card-front .brand {
    position: absolute; left: 0; right: 0; top: 110px;
    justify-content: center;
  }
  .front-url {
    position: absolute; left: 0; right: 0; bottom: 74px;
    text-align: center; color: var(--white);
    font-weight: 700; font-size: 17px; letter-spacing: 0.3px;
  }
  .service-band {
    position: absolute; left: 0; right: 0; bottom: 0; height: 56px;
    background: var(--orange);
    display: flex; align-items: center; justify-content: center;
    color: var(--white); font-weight: 700; font-size: 17px; gap: 10px;
  }
  .service-band .sep { font-size: 14px; }

  /* Back */
  .card-back {
    left: 510px; top: 520px;
    background: var(--white);
  }
  .back-top {
    position: absolute; left: 0; right: 0; top: 0; height: 160px;
    background: linear-gradient(180deg, #ffffff 0%, #f1f2f4 100%);
  }
  .card-back .brand {
    position: absolute; left: 0; right: 0; top: 54px;
    justify-content: center;
  }
  .back-rule {
    position: absolute; left: 0; right: 0; top: 160px; height: 7px;
    background: var(--orange);
  }
  .back-panel {
    position: absolute; left: 0; right: 0; top: 167px; bottom: 0;
    background: radial-gradient(ellipse at 50% 30%, var(--navy-light) 0%, var(--navy) 50%, var(--navy-deep) 100%);
    color: var(--white); text-align: center;
    padding-top: 14px;
  }
  .person { font-size: 0; margin-bottom: 6px; }
  .person-name {
    font-weight: 700; font-size: 22px; color: var(--orange);
  }
  .person-title {
    font-style: italic; font-size: 13px; color: var(--white); margin-left: 8px;
  }
  .contact-line {
    font-size: 14.5px; line-height: 23px; color: var(--white);
  }
  .contact-line .dot { margin: 0 6px; }
</style>
</head>
<body>
<main class="canvas">

  <section class="card card-front" aria-label="Business card front">
    <div class="brand">
      <span class="brand-dot"></span>
      <span class="brand-name">Trelvan Media</span>
    </div>
    <p class="front-url">www.trelvanmedia.example</p>
    <div class="service-band">
      <span>Web Design</span><span class="sep">•</span>
      <span>Internet Marketing</span><span class="sep">•</span>
      <span>Website Management</span>
    </div>
  </section>

  <section class="card card-back" aria-label="Business card back">
    <div class="back-top"></div>
    <div class="brand">
      <span class="brand-dot"></span>
      <span class="brand-name">Trelvan Media</span>
    </div>
    <div class="back-rule"></div>
    <div class="back-panel">
      <p class="person"><span class="person-name">Mark Lenner</span><span class="person-title">President/CEO</span></p>
      <p class="contact-line">mark@trelvanmedia.example</p>
      <p class="contact-line">Phone: 520-381-7459<span class="dot">•</span>Toll Free: 866-381-7459</p>
      <p class="contact-line">Twitter@trelvanmedia<span class="dot">•</span>www.facebook.com/trelvanmedia</p>
      <p class="contact-line">4315 W. Calloway Ave. Ste. 140 Tucson, AZ 85792</p>
    </div>
  </section>

</main>
</body>
</html>
```